Tavrenne Capital LLC

Need Professional Business cards for New Investment Fund

Target Market(s)

High Quality investors

Industry/Entity Type

Financial

Contact Information for Business Card

Phone Number +1 555 284 6190
Name Lukas Varenko
Title Fund Manager
email lv@FundTavrenne.com
Website www.FundTavrenne.com

Colors

Designer to choose colors to be used in the design.

Requirements
Must have
• Must have our Logo and all of the above. Must be made so lettering and loge can be raised

```html
<!DOCTYPE html>
<html lang="en">
<head>
<meta charset="UTF-8">
<title>Tavrenne Capital – Business Card</title>
<link href="https://fonts.googleapis.com/css2?family=Montserrat:wght@400;500;600&display=swap" rel="stylesheet">
<style>
  :root {
    --stage: #2b302c;
    --card: #ffffff;
    --card-shade: #eeeeee;
    --green: #17d317;
    --forest: #353d35;
    --ink: #3c3f3c;
  }
  html, body {
    margin: 0;
    width: 1200px;
    height: 900px;
    overflow: hidden;
    background: var(--stage);
    font-family: "Montserrat", sans-serif;
  }
  .card {
    position: absolute;
    left: 100px;
    top: 165px;
    width: 1000px;
    height: 570px;
    background: linear-gradient(160deg, var(--card) 40%, var(--card-shade) 100%);
    overflow: hidden;
  }
  .card-art {
    position: absolute;
    inset: 0;
  }
  .holder {
    position: absolute;
    left: 150px;
    top: 150px;
  }
  .holder-name {
    margin: 0;
    color: var(--green);
    font-size: 30px;
    font-weight: 500;
    letter-spacing: 0.5px;
    text-transform: uppercase;
    white-space: nowrap;
  }
  .holder-title {
    margin: 4px 0 0;
    color: var(--ink);
    font-size: 22px;
    font-weight: 400;
  }
  .contacts {
    position: absolute;
    left: 150px;
    top: 300px;
    margin: 0;
    padding: 0;
    list-style: none;
    color: var(--ink);
    font-size: 22px;
    line-height: 36px;
  }
  .contacts li {
    display: flex;
    align-items: center;
    gap: 12px;
    white-space: nowrap;
  }
  .contacts svg {
    width: 16px;
    height: 16px;
    flex: none;
  }
  .address {
    position: absolute;
    left: 470px;
    top: 420px;
    margin: 0;
    color: var(--ink);
    font-size: 22px;
    line-height: 34px;
    font-style: normal;
    white-space: nowrap;
  }
  .brand {
    position: absolute;
    left: 540px;
    top: 230px;
    display: flex;
    align-items: center;
    gap: 14px;
    color: var(--forest);
    font-size: 38px;
    font-weight: 600;
    letter-spacing: 2px;
    text-transform: uppercase;
    white-space: nowrap;
  }
  .brand-square {
    width: 24px;
    height: 24px;
    background: var(--forest);
  }
</style>
</head>
<body>
  <section class="card" aria-label="Tavrenne Capital LLC business card">
    <svg class="card-art" viewBox="0 0 1000 570" aria-hidden="true">
      <rect class="edge-band" x="0" y="0" width="90" height="570" fill="var(--green)"/>
      <rect class="edge-line" x="100" y="0" width="6" height="570" fill="var(--green)"/>
      <polygon class="corner-dark" points="1000,260 1000,570 700,570" fill="var(--forest)"/>
      <polygon class="corner-green" points="1000,420 1000,570 830,570" fill="var(--green)"/>
    </svg>

    <div class="holder">
      <h1 class="holder-name">Lukas Varenko</h1>
      <p class="holder-title">Fund Manager</p>
    </div>

    <ul class="contacts">
      <li>
        <svg viewBox="0 0 16 16"><path d="M4 1l3 3-2 2c1 2 3 4 5 5l2-2 3 3-2 3C7 15 1 9 1 3z" fill="var(--green)"/></svg>
        +1 555 284 6190
      </li>
      <li>
        <svg viewBox="0 0 16 16"><rect x="1" y="3" width="14" height="10" fill="none" stroke="var(--green)" stroke-width="1.6"/><path d="M1 3l7 6 7-6" fill="none" stroke="var(--green)" stroke-width="1.6"/></svg>
        lv@FundTavrenne.com
      </li>
      <li>
        <svg viewBox="0 0 16 16"><circle cx="8" cy="8" r="7" fill="none" stroke="var(--green)" stroke-width="1.6"/><path d="M1 8h14M8 1c-3 4-3 10 0 14M8 1c3 4 3 10 0 14" fill="none" stroke="var(--green)" stroke-width="1.2"/></svg>
        www.FundTavrenne.com
      </li>
    </ul>

    <address class="address">
      48 Alder Row,<br>
      Millbrook, NJ, 07099
    </address>

    <div class="brand">
      <span class="brand-square"></span>
      Tavrenne
    </div>
  </section>
</body>
</html>
```